Biz Card Design TVCP

New business card for a new company.
Logo was completed by a designer on ArtHarbor and looking to continue requesting additional services.
Company Name: Tidal Vector Power Consulting
Although this company is starting in Canada, we will be moving towards a global presence within the next 6 months.
Key elements to this business are as follows.
Energy Procurement
Energy Reduction Services
Demand Side Consulting
Energy Efficiency Consulting
Saving Clients Money
Helping Them Go "Green"
Managing Their Energy Requirements
Basically the goal for our company is to find the best procurement solution for our clients and reduce their energy consumption. This reduces their expenses and the amount of greenhouse gas they produce on a daily basis.
I have been in the energy footprint for the last 20 years and know that most companies are looking to "do whatever is necessary to get them to sign on the dotted line". I would prefer to walk away from a client that I can't help than to put them into a situation that they will regret for years to come. This is where the "TIDAL" part of the company name comes from.
The following is a catch phrase that encompasses what we do.
"Reducing your carbon footprint & energy bill at the same time!"
The back of the card needs to have this statement along with some sort of illustration. The back is a playground for creative ideas.
The front of the card needs the following.
Logo.
First & Last Name (Gus Marwick)
Title (Energy Warrior)
Phone Number (555) 314-2718
Fax Number (555) 271-8314
Email Address gus@tidalvectorpowerconsulting.example
Address 47 fenwick rd Toronto Ontario K4T 2P9
I want it to be a card that is remembered when any of my staff give it to a customer. It HAS to stand out.
Target Market(s)
Business Owners, Decision Makers, 30 to 65+
Industry/Entity Type
Business
Look and feel

```html
<!DOCTYPE html>
<html lang="en">
<head>
<meta charset="utf-8">
<title>Tidal Vector Power Consulting – Business Card</title>
<link rel="stylesheet" href="https://fonts.googleapis.com/css2?family=Cabin:wght@400;600&display=swap">
<style>
  :root {
    --stage: #000000;
    --front-deep: #04121e;
    --front-mid: #0a2234;
    --accent-blue: #3a9ad6;
    --brand-blue: #1f74d4;
    --ornament-a: #0c3556;
    --ornament-b: #082338;
    --back-paper: #ffffff;
    --ink: #262626;
    --rule: #1b3a5c;
    --leaf-light: #9be6a8;
    --leaf-deep: #2faa55;
  }
  html, body {
    margin: 0;
    padding: 0;
    width: 1200px;
    height: 938px;
    overflow: hidden;
    background: var(--stage);
    font-family: "Cabin", "Candara", sans-serif;
  }
  .canvas {
    position: relative;
    width: 1200px;
    height: 938px;
    background: var(--stage);
  }
  .card {
    position: absolute;
    width: 734px;
    height: 378px;
    box-sizing: border-box;
    overflow: hidden;
  }
  .card--front {
    left: 101px;
    top: 84px;
    background: linear-gradient(135deg, var(--front-mid) 0%, var(--front-deep) 70%);
  }
  .front__ornament {
    position: absolute;
    left: 4px;
    top: 0;
    width: 184px;
    height: 378px;
    background: linear-gradient(180deg, var(--ornament-a), var(--ornament-b));
    opacity: 0.75;
  }
  .front__name,
  .front__title {
    position: absolute;
    right: 18px;
    margin: 0;
    color: var(--accent-blue);
    font-size: 23px;
    font-weight: 400;
  }
  .front__name { top: 26px; }
  .front__title { bottom: 22px; }
  .front__brand {
    position: absolute;
    left: 0;
    right: 0;
    top: 160px;
    margin: 0;
    text-align: center;
    color: var(--brand-blue);
    font-size: 44px;
    font-weight: 600;
    letter-spacing: 0.5px;
  }
  .card--back {
    left: 408px;
    top: 462px;
    background: var(--back-paper);
    color: var(--ink);
  }
  .back__brand {
    position: absolute;
    left: 14px;
    top: 128px;
    width: 220px;
    margin: 0;
    text-align: center;
    color: var(--brand-blue);
    font-size: 22px;
    font-weight: 600;
    line-height: 1.25;
  }
  .back__rule {
    position: absolute;
    left: 251px;
    top: 27px;
    width: 2px;
    height: 323px;
    background: var(--rule);
  }
  .contact {
    position: absolute;
    left: 275px;
    margin: 0;
    font-size: 19px;
    line-height: 27px;
  }
  .contact__row { display: flex; }
  .contact__label { white-space: pre; }
  .contact--phones { top: 30px; }
  .contact--phones .contact__label { width: 126px; }
  .contact--phones .contact__row--fax .contact__label { width: 132px; }
  .contact--mail { top: 262px; }
  .contact--mail .contact__label { width: 66px; }
  .contact--mail .contact__row--address .contact__label { width: 90px; }
  .back__illustration {
    position: absolute;
    left: 275px;
    top: 104px;
    width: 48px;
    height: 48px;
    border-radius: 50%;
    background: radial-gradient(circle at 35% 35%, var(--leaf-light), var(--leaf-deep));
  }
  .back__tagline {
    position: absolute;
    left: 336px;
    top: 102px;
    width: 370px;
    margin: 0;
    color: var(--leaf-deep);
    font-size: 18px;
    font-weight: 600;
    line-height: 25px;
  }
</style>
</head>
<body>
<main class="canvas">
  <section class="card card--front" aria-label="Card front">
    <div class="front__ornament" role="img" aria-label="Large faint currency symbol decoration"></div>
    <p class="front__name">Gus Marwick</p>
    <h1 class="front__brand">Tidal Vector Power Consulting</h1>
    <p class="front__title">Energy Warrior</p>
  </section>

  <section class="card card--back" aria-label="Card contact side">
    <p class="back__brand">Tidal Vector Power Consulting</p>
    <div class="back__rule"></div>
    <div class="contact contact--phones">
      <div class="contact__row"><span class="contact__label">Phone no:-</span><span>(555) 314-2718</span></div>
      <div class="contact__row contact__row--fax"><span class="contact__label">Fax Number:-</span><span>(555) 271-8314</span></div>
    </div>
    <div class="back__illustration" role="img" aria-label="Green energy illustration"></div>
    <p class="back__tagline">“Reducing your carbon footprint &amp; energy bill at the same time!”</p>
    <div class="contact contact--mail">
      <div class="contact__row"><span class="contact__label">Email:-</span><span>gus@tidalvectorpowerconsulting.example</span></div>
      <div class="contact__row contact__row--address"><span class="contact__label">Address:-</span><span>47 fenwick rd Toronto<br>Canada K4T 2P9</span></div>
    </div>
  </section>
</main>
</body>
</html>
```